Lorvex Tilo medical cannibis cultivation company

tag - Tilo rise
Lorvex Tilo medical cannabis cultivation - logo is selected- can we please see bold examples with our selection. We are mainly dealing with medical companies and professionals. We would like to be stand out in the crowd with our designs. Welcome any and all attempts. Thanks

Target Market(s)

Medical and Professional

Industry/Entity Type

Medical And Science

Font styles to use
Sans Serif

Colors

Designer to choose colors to be used in the design.

Requirements
Must have
• Bright colour and be bold- Love the teal and magenta that is currently on the dark background design.
Nice to have
• shading and the 3D affect- The shadowed appearance.
Should not have
• Anything related to illegal activity or un professional manners

```html
<!DOCTYPE html>
<html lang="en">
<head>
<meta charset="utf-8">
<title>Lorvex Tilo – Business Card</title>
<link rel="stylesheet" href="https://fonts.googleapis.com/css2?family=Cinzel:wght@400;600&family=Roboto:wght@400;500;700&display=swap">
<style>
  :root {
    --page: #e8e5df;
    --card: #0b0b0c;
    --teal: #1fb5e8;
    --magenta: #a24cb0;
    --ring: #8a8d92;
    --tag-grey: #b9bcc0;
    --white: #ffffff;
  }
  * { box-sizing: border-box; margin: 0; padding: 0; }
  html, body { width: 1200px; height: 1040px; overflow: hidden; }
  body {
    background: var(--page);
    font-family: "Roboto", Arial, sans-serif;
    display: flex;
    flex-direction: column;
    align-items: center;
    justify-content: center;
    gap: 60px;
  }
  .card {
    position: relative;
    width: 700px;
    height: 400px;
    background: var(--card);
    border-radius: 22px;
    overflow: hidden;
    box-shadow: 0 18px 34px rgba(0,0,0,0.35);
  }
  .wordmark { position: absolute; text-align: center; }
  .wordmark__name {
    font-family: "Cinzel", Georgia, serif;
    font-weight: 600;
    font-size: 44px;
    letter-spacing: 1px;
    color: var(--teal);
    line-height: 1;
    white-space: nowrap;
  }
  .wordmark__tag {
    display: flex;
    align-items: center;
    gap: 10px;
    margin-top: 6px;
    font-family: "Cinzel", Georgia, serif;
    font-size: 16px;
    letter-spacing: 4px;
    color: var(--tag-grey);
  }
  .wordmark__tag::before, .wordmark__tag::after {
    content: ""; flex: 1; height: 1px; background: var(--tag-grey);
  }
  .front .wordmark { left: 60px; top: 72px; width: 330px; }
  .band { position: absolute; }
  .band--magenta { left: 360px; right: 0; top: 150px; height: 180px; background: var(--magenta); }
  .band--teal { left: 150px; width: 210px; top: 250px; bottom: 0; background: var(--teal); }
  .emblem {
    position: absolute;
    width: 124px; height: 124px;
    border-radius: 50%;
    background: var(--card);
    border: 4px solid var(--ring);
  }
  .front .emblem { left: 298px; top: 188px; }
  .contacts {
    position: absolute;
    right: 30px; top: 178px;
    list-style: none;
    color: var(--white);
    font-size: 17px;
    line-height: 30px;
    text-align: right;
  }
  .contacts li { display: flex; align-items: center; justify-content: flex-end; gap: 10px; }
  .contacts svg { width: 16px; height: 16px; fill: var(--white); }
  .person {
    position: absolute;
    left: 170px; top: 290px;
    color: var(--white);
  }
  .person__name { font-size: 22px; font-weight: 700; letter-spacing: 0.5px; }
  .person__role { font-size: 16px; font-weight: 500; margin-bottom: 6px; }
  .person__address { font-size: 14px; line-height: 19px; }
  .back .wordmark { left: 130px; top: 160px; width: 330px; }
  .back .emblem { left: 470px; top: 138px; }
</style>
</head>
<body>

<section class="card front">
  <div class="wordmark">
    <div class="wordmark__name">LORVEX TILO</div>
    <div class="wordmark__tag">TILO RISE</div>
  </div>

  <div class="band band--magenta"></div>
  <div class="band band--teal"></div>
  <div class="emblem"></div>

  <ul class="contacts">
    <li>555 210 4816
      <svg viewBox="0 0 16 16"><path d="M4 1l3 3-2 2c1 2 3 4 5 5l2-2 3 3-2 2C8 14 2 8 2 3z"/></svg>
    </li>
    <li>555 730 2291
      <svg viewBox="0 0 16 16"><path d="M4 0h8a1 1 0 0 1 1 1v14a1 1 0 0 1-1 1H4a1 1 0 0 1-1-1V1a1 1 0 0 1 1-1zm1 2v10h6V2z"/></svg>
    </li>
    <li>nora@lorvextilo.com
      <svg viewBox="0 0 16 16"><path d="M1 3h14v10H1zm1.5 1.2V12h11V4.2L8 8.5z"/></svg>
    </li>
    <li>www.lorvextilo.com
      <svg viewBox="0 0 16 16"><circle cx="8" cy="8" r="7"/><path d="M1 8h14M8 1c3 3 3 11 0 14M8 1c-3 3-3 11 0 14" stroke="#a24cb0" stroke-width="1.2" fill="none"/></svg>
    </li>
  </ul>

  <div class="person">
    <div class="person__name">NORA VALE</div>
    <div class="person__role">CEO/FOUNDER</div>
    <div class="person__address">412 Alder Court<br>Fairview, Ontario 20418</div>
  </div>
</section>

<section class="card back">
  <div class="wordmark">
    <div class="wordmark__name">LORVEX TILO</div>
    <div class="wordmark__tag">TILO RISE</div>
  </div>
  <div class="emblem"></div>
</section>

</body>
</html>
```